Need Primer (paint) Label Design

THE ATTACHED LABEL/S ARE SOLEY FOR REFERENCE. DO NOT MAKE ME AN INTERIOR PAINT OR CHALK PAINT LABEL. I ONLY NEED A "PRIMER" LABEL. THE ATTACHED INTERIOR PAINT LABEL IS ONLY TO SHOW YOU THE THEME/DESIGN OF OUR OTHER LABELS. THE BLUE LABEL ONLY HAS A DESIGN ASPECT I LIKE (PRIMER ON SIDE). The last four labels are our competitors.
```````````````````````````````````````````````````````````````````````````````````````````````````
We need this label to look professional, sharp, eye catching and modern.
OUR PRIMARY COLORS ARE BLACK AND WHITE. IF YOU INCOPORATE ANOTHER COLOR, SILVER OR GOLD MIGHT BE IDEAL BUT PLEASE DON'T DRIFT TOO FAR.
The attached documents:
1st - Our Logo
2nd - Our chalk paint label (reference). We do not need a chalk paint label.
3rd. A random design example. I like the PRIME on the side running vertically. I think it's a cool design concept.
````````````````````````````````````````````````````````````````````````````````````````````````````
We are going to be using a normal paint can with a metal bail/handle so please use that with you design work
``````````````````````````````````````````````````````````````````````````````````````````````````
Order, in my head:
4376
Coatings
^^ I want this to stand out as well but I don't want it to be the first thing your eye is drawn to. Probably 2nd
Interior/Exterior
Multi - Surface Primer
^^ Want this to stick out and draw your eye so the customer knows what it is immediately
Exceptional Adhesion, Performance, Durability,
Use on Wood, Drywall, Plaster, Stucco, Masonry, Brick, Paneling, Painted Metal, & Properly Prepared Glossy Surfaces & More
35* Lowe Temperature Application (can be on side or small)
100% Acrylic
Low Odor - Low VOC - Soap & Water Clean Up
1 US Gallon - 3.785 L
Feel free to get creative with it!

```html
<!DOCTYPE html>
<html lang="en">
<head>
<meta charset="utf-8">
<title>4376 Coatings – Multi Surface Primer Label</title>
<link href="https://fonts.googleapis.com/css2?family=Archivo:wght@500;600;700&display=swap" rel="stylesheet">
<style>
  :root {
    --ink: #000000;
    --paper: #ffffff;
    --band-light: #5a5a5a;
    --rule: #bdbdbd;
  }
  * { margin: 0; padding: 0; box-sizing: border-box; }
  html, body { width: 1200px; height: 1200px; overflow: hidden; background: var(--paper); }
  body { font-family: "Archivo", Arial, sans-serif; color: var(--paper); position: relative; }

  .label {
    position: absolute; left: 139px; top: 141px; width: 936px; height: 860px;
    background: var(--ink);
    box-shadow: 6px 6px 5px rgba(0,0,0,.45);
    overflow: hidden;
  }
  .brand-name {
    position: absolute; left: 115px; top: 170px; width: 500px; text-align: center;
    font-size: 50px; line-height: 1; font-weight: 600; color: var(--paper);
  }

  .feature-band {
    position: absolute; left: 0; top: 320px; width: 655px; height: 296px;
    background: linear-gradient(90deg, var(--ink) 0%, #262626 50%, var(--band-light) 100%);
  }
  .side-band {
    position: absolute; left: 655px; top: 177px; width: 227px; bottom: 0;
    background: linear-gradient(180deg, #050505 0%, #3a3a3a 35%, #686868 65%, #6a6a6a 100%);
  }
  .centered { position: absolute; left: 59px; width: 600px; text-align: center; }
  .use-type { top: 343px; font-size: 37px; font-weight: 600; letter-spacing: .5px; }
  .benefits { top: 408px; font-size: 27px; line-height: 36px; font-weight: 600; }
  .divider { position: absolute; left: 160px; top: 528px; width: 420px; height: 1px; background: var(--rule); }
  .surfaces { top: 552px; font-size: 13.5px; line-height: 19px; font-weight: 600; }
  .care { top: 637px; font-size: 15px; font-weight: 600; }

  .acrylic { position: absolute; left: 84px; top: 725px; font-size: 40px; line-height: 44px; font-weight: 600; }
  .volume { position: absolute; left: 424px; top: 748px; width: 180px; text-align: center; font-size: 25px; line-height: 33px; font-weight: 600; }

  .temp-note { position: absolute; left: 671px; top: 70px; font-size: 16px; line-height: 21px; font-weight: 600; }

  .product-title { position: absolute; left: 0; top: 0; width: 936px; height: 860px; }
  .product-title text { font-family: "Archivo", Arial, sans-serif; font-weight: 600; fill: var(--paper); font-size: 96px; }
</style>
</head>
<body>
  <div class="label">
    <div class="side-band"></div>
    <div class="feature-band"></div>

    <div class="brand-name">4376 Coatings</div>

    <div class="temp-note">35*<br>Lowe<br>Temperature<br>Application</div>

    <div class="centered use-type">INTERIOR/EXTERIOR</div>
    <div class="centered benefits">Exceptional Adhesion<br>Performance<br>Durability</div>
    <div class="divider"></div>
    <div class="centered surfaces">Use on Wood, Drywall, Plaster, Stucco, Masonry, Brick, Paneling,<br>Painted Metal, &amp; Properly Prepared Glossy Surfaces &amp; More</div>
    <div class="centered care">Low Odor - Low VOC -&nbsp; Soap &amp; Water Clean Up</div>

    <div class="acrylic">100%<br>Acrylic</div>
    <div class="volume">1 US Gallon<br>3.785 L</div>

    <svg class="product-title" viewBox="0 0 936 860" aria-label="Multi Surface Primer">
      <text transform="translate(746 806) rotate(-90)" textLength="217" lengthAdjust="spacingAndGlyphs">MULTI</text>
      <text transform="translate(857 806) rotate(-90)" textLength="740" lengthAdjust="spacingAndGlyphs">SURFACE PRIMER</text>
    </svg>
  </div>
</body>
</html>
```